New Company Business Card design

Looking for a corporate looking business card utilising my new logo design - the logo i would like embossed as one option and flat as another - simplistic but stylish - less is more - we are an import export business launching into the market - i would like a couple of options as main background - Grey or Black

```html
<!DOCTYPE html>
<html lang="en">
<head>
<meta charset="utf-8">
<title>Meridian Trade Partners – Business Card</title>
<link rel="stylesheet" href="https://fonts.googleapis.com/css2?family=Cinzel:wght@500&family=Arimo:wght@400&display=swap">
<style>
  :root {
    --stage: #2b2b2d;
    --card: #0b0b0c;
    --brand-blue: #1c78c8;
    --steel-grey: #6e6e72;
    --text-light: #e6e6e6;
    --text-muted: #8a8a8e;
  }
  * { margin: 0; padding: 0; box-sizing: border-box; }
  html, body {
    width: 1200px; height: 782px; overflow: hidden;
    background: var(--stage);
  }
  .stage {
    position: relative; width: 1200px; height: 782px;
    display: flex; align-items: center; justify-content: center; gap: 40px;
  }
  .card {
    position: relative; width: 540px; height: 309px;
    background: var(--card); overflow: hidden;
    box-shadow: 0 12px 30px rgba(0,0,0,.45);
  }
  /* front */
  .front .lockup {
    position: absolute; inset: 0;
    display: flex; flex-direction: column; align-items: center; justify-content: center;
  }
  .brand-name {
    font-family: "Cinzel", serif; font-weight: 500;
    color: var(--brand-blue); font-size: 30px; letter-spacing: 1px;
  }
  .front .rule {
    width: 380px; height: 1px; background: var(--steel-grey); margin: 10px 0 8px;
  }
  .tagline {
    font-family: "Cinzel", serif; font-size: 11px; letter-spacing: 3px;
    color: var(--text-muted); text-transform: uppercase;
  }
  /* back */
  .back .person { position: absolute; left: 30px; top: 34px; }
  .person-name {
    font-family: "Cinzel", serif; font-weight: 500;
    color: var(--brand-blue); font-size: 19px; letter-spacing: 1px;
  }
  .person-role {
    font-family: "Arimo", sans-serif; font-size: 12px; color: var(--text-light); margin-top: 2px;
  }
  .contacts {
    position: absolute; left: 30px; top: 160px; list-style: none;
    font-family: "Arimo", sans-serif; font-size: 13px; color: var(--text-light);
  }
  .contacts li { display: flex; align-items: center; gap: 8px; line-height: 19px; }
  .contacts svg { width: 11px; height: 11px; fill: var(--text-light); flex: none; }
  .back .brand-name {
    position: absolute; right: 36px; top: 120px; font-size: 24px;
  }
  .address {
    position: absolute; right: 34px; bottom: 50px; text-align: left;
    font-family: "Arimo", sans-serif; font-size: 13px; color: var(--text-light); line-height: 18px;
  }
  .bands { position: absolute; left: 0; bottom: 0; width: 540px; height: 40px; }
</style>
</head>
<body>
<main class="stage">

  <section class="card front" aria-label="Card front">
    <div class="lockup">
      <div class="brand-name">Meridian Trade Partners</div>
      <div class="rule"></div>
      <div class="tagline">Worldwide Supply for Local Markets</div>
    </div>
  </section>

  <section class="card back" aria-label="Card back">
    <div class="person">
      <div class="person-name">DORIAN KELL</div>
      <div class="person-role">Managing Director</div>
    </div>

    <ul class="contacts">
      <li><svg viewBox="0 0 12 12"><path d="M2 1h3l1 3-1.5 1a7 7 0 0 0 2.5 2.5L8 6l3 1v3c0 .6-.4 1-1 1A9 9 0 0 1 1 2c0-.6.4-1 1-1z"/></svg>055-210 384 617</li>
      <li><svg viewBox="0 0 12 12"><path d="M3 0h6a1 1 0 0 1 1 1v10a1 1 0 0 1-1 1H3a1 1 0 0 1-1-1V1a1 1 0 0 1 1-1zm0 1.5v8h6v-8z"/></svg>055-210 384 618</li>
      <li><svg viewBox="0 0 12 12"><path d="M0 2h12v8H0zm1 1v.4l5 3.2 5-3.2V3z"/></svg>info@meridiantrade.com</li>
      <li><svg viewBox="0 0 12 12"><circle cx="6" cy="6" r="5.5"/></svg>www.meridiantrade.com</li>
    </ul>

    <div class="brand-name">Meridian Trade Partners</div>

    <div class="address">4821, Harbour Lane<br>Portmere, 560218</div>

    <svg class="bands" viewBox="0 0 540 40" preserveAspectRatio="none" aria-hidden="true">
      <polygon points="0,0 250,0 236,18 0,18" fill="var(--brand-blue)"/>
      <polygon points="262,10 540,10 540,40 244,40" fill="var(--steel-grey)"/>
    </svg>
  </section>

</main>
</body>
</html>
```